Business Card design for law firm = Brightvale Australia

We are seeking a new design for our business cards.
We are keeping our logo, which is attached.
We need space for
Name
Title
Address is , which is
Level 7
214 Marlowe Street
Sydney NSW 2047
Phone :
Mobile :
Fax :
Email :
DX :
website www.brightvale-example.com.au

Industry/Entity Type

Law Firm / Banking and Finance

Contact Information for Business Card

We are seeking a new design for our business cards. We are keeping our logo. We need space for Name Title Address is Level 7 214 Marlowe Street Sydney NSW 2047 Phone Mobile Fax Email DX website www.brightvale-example.com.au

Colors
0054AA
0677BA
7BADD7
CADEEF
E8F1F8

Requirements
Must have
• see our website for general feel www.brightvale-example.com.au

```html
<!DOCTYPE html>
<html lang="en">
<head>
<meta charset="utf-8">
<title>Brightvale Australia — Business Card</title>
<link rel="stylesheet" href="https://fonts.googleapis.com/css2?family=EB+Garamond:ital,wght@0,400;1,400&display=swap">
<style>
  :root {
    --backdrop: #2b2b2b;
    --front-blue: #2e4f98;
    --front-blue-deep: #284789;
    --accent-cyan: #0e8fc4;
    --ink-blue: #22449a;
    --paper: #ececec;
    --paper-shade: #dcdcdc;
    --ink: #2f2f2f;
    --light-text: #e9ecf3;
  }
  * { margin: 0; padding: 0; box-sizing: border-box; }
  html, body {
    width: 1200px; height: 1138px; overflow: hidden;
    background: var(--backdrop);
    font-family: "EB Garamond", Georgia, serif;
  }
  .canvas { position: relative; width: 1200px; height: 1138px; }

  .card {
    position: absolute; width: 620px; height: 376px;
    border-radius: 16px; overflow: hidden;
    box-shadow: 0 6px 14px rgba(0,0,0,0.45);
  }

  /* front */
  .card-front {
    left: 272px; top: 184px;
    background: linear-gradient(180deg, var(--front-blue-deep), var(--front-blue));
  }
  .front-name {
    position: absolute; left: 0; width: 100%; top: 168px;
    text-align: center; font-size: 56px; line-height: 1;
    color: var(--light-text); font-weight: 400;
  }
  .front-web {
    position: absolute; left: 0; width: 100%; top: 334px;
    text-align: center; font-size: 14px; letter-spacing: 0.45em;
    color: var(--light-text);
  }
  .front-bar {
    position: absolute; left: 142px; bottom: 0;
    width: 340px; height: 9px; background: var(--accent-cyan);
  }

  /* back */
  .card-back {
    left: 274px; top: 606px;
    background: linear-gradient(180deg, var(--paper), var(--paper-shade));
  }
  .holder-name {
    position: absolute; left: 32px; top: 42px;
    font-size: 29px; font-weight: 400; color: var(--ink-blue); line-height: 1;
  }
  .holder-rule { position: absolute; left: 20px; top: 74px; }
  .holder-title {
    position: absolute; left: 32px; top: 82px;
    font-size: 16px; font-style: italic; color: var(--ink);
  }
  .address {
    position: absolute; left: 32px; top: 208px;
    font-size: 15.5px; line-height: 20px; color: var(--ink);
  }
  .contacts {
    position: absolute; left: 32px; top: 258px;
    list-style: none; font-size: 15.5px; line-height: 20px; color: var(--ink);
  }
  .contacts li { display: flex; align-items: center; }
  .contacts svg { width: 12px; height: 12px; margin-right: 18px; fill: var(--accent-cyan); }
  .back-name {
    position: absolute; right: 26px; top: 272px;
    font-size: 42px; line-height: 1; color: var(--ink-blue);
  }
</style>
</head>
<body>
<main class="canvas">
  <section class="card card-front">
    <div class="front-name">Brightvale</div>
    <div class="front-web">www.brightvale-example.com.au</div>
    <div class="front-bar"></div>
  </section>

  <section class="card card-back">
    <h1 class="holder-name">Sam Whitford</h1>
    <svg class="holder-rule" width="160" height="6" viewBox="0 0 160 6">
      <path d="M0 4 Q80 1 160 2" stroke="var(--ink-blue)" stroke-width="2.5" fill="none" stroke-linecap="round"/>
    </svg>
    <p class="holder-title">Managing Director</p>

    <p class="address">Level 7 214 Marlowe St<br>Sydney NSW 2047</p>

    <ul class="contacts">
      <li><svg viewBox="0 0 12 12"><path d="M1 4 Q6 0 11 4 L9 5.5 L8 4 H4 L3 5.5 Z M3 6 H9 L10 11 H2 Z"/></svg>02 9000 0122</li>
      <li><svg viewBox="0 0 12 12"><path d="M3 0 H9 V3 H3 Z M0 4 H12 V9 H10 V7 H2 V9 H0 Z M3 8 H9 V12 H3 Z"/></svg>02 9000 6411</li>
      <li><svg viewBox="0 0 12 12"><path d="M0 2 H12 V10 H0 Z" fill="none" stroke="var(--accent-cyan)" stroke-width="1.4"/><path d="M0 2 L6 7 L12 2" fill="none" stroke="var(--accent-cyan)" stroke-width="1.4"/></svg>sam.whitford@brightvale-example.com.au</li>
      <li><svg viewBox="0 0 12 12"><circle cx="6" cy="6" r="5.3" fill="none" stroke="var(--accent-cyan)" stroke-width="1.2"/><path d="M1 6 H11 M6 1 V11 M6 1 Q2 6 6 11 M6 1 Q10 6 6 11" fill="none" stroke="var(--accent-cyan)" stroke-width="1"/></svg>www.brightvale-example.com.au</li>
    </ul>

    <div class="back-name">Brightvale</div>
  </section>
</main>
</body>
</html>
```